Brand new letterhead, business card, email signature etc.

We are a financial company in London, UK. Our website is www.marlowvane.com. We're wanting a complete remodel of the company colours, letter head, business cards, email signatures, etc. Looking to keep the same font for the company name. I have upload a colour palette that we want to work with. We're looking for company letterhead for outgoing letters/ correspondence, letterhead for internal documentation, email signatures, e-letters. etc. Ultimately we will redesign the entire website also. It is important that our clients get a strong, secure, warm, trustworthy, solid feeling and first impression.
Updates

Designs look the same

Target Market(s)

Institutional investors, (ultra) high net worth individuals

Industry/Entity Type

Finance, Invesments banking.

Font styles to use
Other font styles liked:
• Current font is "Champagne & Limousines"

Requirements
Must have
• Must use the colours provided on the PDF uploaded to the portal. The purple = main colour. The red = accent colour.
Nice to have
• Nice to use same font as now for the company name "Corvane". Font is "Champagne & Limousines". Nice to have some reference to the old logo flower, but only subtle.
Should not have
• Do not use the colour red from our website. Use the colours provided on the colour palette PDF that I uploaded in the portal.

```html
<!DOCTYPE html>
<html lang="en">
<head>
<meta charset="utf-8">
<title>Corvane – Corporate Information</title>
<link href="https://fonts.googleapis.com/css2?family=Quicksand:wght@300;400;500;600&display=swap" rel="stylesheet">
<style>
  :root {
    --canvas: #ffffff;
    --paper: #fcfaf9;
    --frame: #8c8789;
    --mauve-strip: #b9afb4;
    --salmon: #f0987a;
    --salmon-line: #f2b7a2;
    --plum: #3a1f2c;
    --body: #a3909a;
    --link: #e2432d;
    --panel-grey: #eeeaeb;
    --panel-peach: #f8e4dc;
    --city-light: #eeeeee;
    --city-dark: #bdbdbd;
  }
  * { margin: 0; padding: 0; box-sizing: border-box; }
  html, body { width: 999px; height: 1200px; overflow: hidden; background: var(--canvas); }
  body { position: relative; font-family: "Quicksand", sans-serif; }

  .eletter {
    position: absolute; left: 255px; top: 183px; width: 491px; height: 837px;
    background: var(--paper); border: 1px solid var(--frame); overflow: hidden;
  }
  .side-strip { position: absolute; left: 0; top: 0; width: 17px; height: 100%; background: var(--mauve-strip); }
  .side-accent { position: absolute; left: 19px; top: 0; width: 2px; height: 100%; background: var(--salmon-line); }

  .masthead {
    position: absolute; left: 20px; top: 0; width: 368px; height: 89px;
    border-bottom: 2px solid #c9c1c4; border-right: 2px solid #c9c1c4;
  }
  .brand { position: absolute; left: 52px; top: 24px; display: flex; align-items: center; gap: 10px; }
  .brand-mark { width: 28px; height: 28px; border: 1px solid var(--plum); }
  .brand-name { font-weight: 300; font-size: 23px; letter-spacing: 4px; color: var(--plum); }

  .skyline {
    position: absolute; left: 20px; top: 91px; width: 368px; height: 214px;
    background: linear-gradient(180deg, var(--city-light) 0%, var(--city-dark) 100%);
    border-bottom: 2px solid #c9c1c4; border-right: 2px solid #c9c1c4;
  }
  .tile { position: absolute; left: 390px; width: 101px; border-left: 1px solid #ddd; }
  .tile-top { top: 0; height: 89px; background: var(--panel-grey); border-bottom: 2px solid #d6cfd2; }
  .tile-mid { top: 90px; height: 127px; background: var(--panel-peach); border-bottom: 2px solid var(--salmon-line); }
  .tile-low { top: 218px; height: 87px; background: var(--panel-grey); }

  .web-rule {
    position: absolute; left: 71px; top: 319px; width: 420px; height: 16px;
    border-top: 1px solid var(--salmon); border-left: 1px solid var(--salmon);
  }
  .web-address { position: absolute; left: 125px; top: 320px; font-size: 12px; font-weight: 600; color: var(--plum); }

  .content { position: absolute; left: 71px; width: 400px; }
  .title { top: 362px; font-size: 30px; font-weight: 500; color: var(--plum); letter-spacing: -0.3px; }
  .lede { top: 413px; font-size: 14.5px; font-weight: 300; color: var(--body); line-height: 18.5px; }

  .cta {
    position: absolute; left: 61px; top: 481px; width: 82px; height: 82px; border-radius: 50%;
    background: var(--salmon); color: var(--plum); font-size: 18px; font-weight: 500;
    line-height: 21px; padding: 20px 0 0 10px;
  }

  .section-title { font-size: 20px; font-weight: 600; color: var(--plum); }
  .section-text { font-size: 14.5px; font-weight: 300; color: var(--body); line-height: 18.5px; }
  .see-more { font-size: 11px; font-weight: 600; color: var(--link); text-decoration: underline; }

  .why-title { top: 577px; }
  .why-text { top: 615px; }
  .why-link { top: 666px; }
  .vision-title { top: 695px; }
  .vision-text { top: 734px; }
  .vision-link { top: 802px; }
</style>
</head>
<body>
  <article class="eletter">
    <div class="side-strip"></div>
    <div class="side-accent"></div>

    <header class="masthead">
      <div class="brand">
        <span class="brand-mark"></span>
        <span class="brand-name">CORVANE</span>
      </div>
    </header>

    <div class="skyline" role="img" aria-label="Pencil sketch of a city street lined with tall skyscrapers"></div>
    <div class="tile tile-top" role="img" aria-label="Faint line-drawn flower petal pattern"></div>
    <div class="tile tile-mid" role="img" aria-label="Peach line-drawn flower petal pattern"></div>
    <div class="tile tile-low" role="img" aria-label="Faint line-drawn flower petal pattern"></div>

    <div class="web-rule"></div>
    <div class="web-address">www.marlowvane.com</div>

    <h1 class="content title">Corporate Information</h1>
    <p class="content lede">Private broking ensures you stay in complete control of your investment decisions without the need to micro-manage every trade.</p>

    <div class="cta">INVEST<br>NOW!</div>

    <h2 class="content section-title why-title">Why Corvane?</h2>
    <p class="content section-text why-text">The Corvane Group of Companies consists of stand alone entities operating under the Corvane banner.</p>
    <a class="content see-more why-link">See More</a>

    <h2 class="content section-title vision-title">Leadership Vision</h2>
    <p class="content section-text vision-text">Corvane was established in anticipation of the need for a high quality, full- service brokerage dedicated to the emerging middle market.</p>
    <a class="content see-more vision-link">See More</a>
  </article>
</body>
</html>
```